PACKAGE DESIGN - Candies - yum!!

NOTE: added Dec 12
I have added a photo below of another product. The element we like is the "stripes" through the packaging. We would like you to consider this element.
Good day all!
Our product is a candy coated chocolate. You'd know them as Q&Z's or Glintos (not the US version of it, but the one everywhere else).
They are small, 1cm diameter. They are available in a bunch of colors. And they are very very tasty!
Need:
(1) One BASE design
(2) 2 different background versions of it (colors) - but we will leave that up to you
(3) the package should be BRIGHT . likely we will make it very glossy.
(4) its a kids product, not some sort of dark chocolate from some obscure plantation in some organic zero emission area. Its just fun chocolate!
(5) we do NOT need a mascot. We want only the product featured and the name
(6) at least ONE of the products has to be broken/open in order to show that its chocolate filled.
PRODUCT NAME:
"ZIP ZAP!"
Colors of the candy (outside):
Red
Purple
Yellow
Green
Blue
Brown
Package Dimensions:
16cm long
7cm high
This should be an easy one! no mascot and simple elliptical multi color candies!
Once we have narrowed down to 2-3 final designs we will ask for slogan etc to be put in.
After we select the winner, we will ask for some small assistance to pie up the package with bar codes etc
Target Market(s)
Kids!
Industry/Entity Type
Product
Requirements
Must have
- MUST HAVE FUN!
If you need some ideas, please look up
"Vorlan Glintos" on findly images.
Q&Zs packaging is too mature for our taste. Something in between the two.
The product will look 90% similar to an Q&Z. 1cm diameter and about 5mm high.

```html
<!DOCTYPE html>
<html lang="en">
<head>
<meta charset="utf-8">
<title>ZIP ZAP – Chocolate Candy Package</title>
<link href="https://fonts.googleapis.com/css2?family=Fredoka:wght@700&family=Crimson+Pro:wght@400&display=swap" rel="stylesheet">
<style>
  :root {
    --orange-deep: #f59a1c;
    --orange-glow: #fdc02a;
    --cream: #fbe9a0;
    --yellow: #ffe600;
    --green: #1fa64a;
    --pink: #e2198a;
    --brown: #5a3217;
    --sky: #1aa8e3;
    --pale: #d8effa;
    --navy: #3c3585;
    --cocoa: #3a2314;
    --purple: #8a2388;
    --candy-yellow: #f7b21f;
    --candy-green: #3aa642;
    --candy-blue: #1fa9ea;
    --candy-pink: #e0148c;
    --candy-brown: #5b3417;
    --white: #ffffff;
  }
  html, body {
    margin: 0;
    padding: 0;
    overflow: hidden;
    background: #ffffff;
  }
  .package {
    position: relative;
    width: 1200px;
    height: 523px;
    overflow: hidden;
    background: radial-gradient(ellipse 70% 55% at 62% 22%, var(--orange-glow) 0%, var(--orange-deep) 75%);
  }
  .package__stripes {
    position: absolute;
    inset: 0;
    width: 1200px;
    height: 523px;
  }
  .candy {
    position: absolute;
    border-radius: 50%;
  }
  .candy--yellow { left: 58px; top: 128px; width: 96px; height: 96px; background: var(--candy-yellow); z-index: 1; }
  .candy--green  { left: 1008px; top: 56px; width: 72px; height: 72px; background: var(--candy-green); }
  .candy--blue   { left: 1081px; top: 45px; width: 90px; height: 90px; background: var(--candy-blue); }
  .candy--pink   { left: 598px; top: 383px; width: 72px; height: 72px; background: var(--candy-pink); }
  .candy--brown  { left: 656px; top: 382px; width: 84px; height: 84px; background: var(--candy-brown); }
  .brand-name {
    position: absolute;
    z-index: 2;
    left: 70px;
    top: 100px;
    width: 990px;
    margin: 0;
    text-align: center;
    font-family: "Fredoka", sans-serif;
    font-weight: 700;
    font-size: 250px;
    line-height: 1;
    letter-spacing: 0;
    color: var(--purple);
  }
  .tagline {
    position: absolute;
    left: 762px;
    top: 408px;
    margin: 0;
    font-family: "Crimson Pro", serif;
    font-weight: 400;
    font-size: 27px;
    line-height: 1.2;
    white-space: nowrap;
    color: var(--white);
    transform: rotate(3deg);
    transform-origin: left center;
  }
</style>
</head>
<body>
  <main class="package">
    <svg class="package__stripes" viewBox="0 0 1200 523" xmlns="http://www.w3.org/2000/svg" aria-hidden="true">
      <path d="M0,278 C350,308 750,255 1200,185 L1200,523 L0,523 Z" fill="var(--cream)"/>
      <path d="M0,301 C350,331 750,295 1200,225 L1200,523 L0,523 Z" fill="var(--yellow)"/>
      <path d="M0,317 C350,347 750,334 1200,264 L1200,523 L0,523 Z" fill="var(--green)"/>
      <path d="M0,341 C350,371 750,367 1200,297 L1200,523 L0,523 Z" fill="var(--pink)"/>
      <path d="M0,354 C350,384 750,387 1200,317 L1200,523 L0,523 Z" fill="var(--brown)"/>
      <path d="M0,396 C350,426 750,411 1200,341 L1200,523 L0,523 Z" fill="var(--sky)"/>
      <path d="M0,420 C350,450 750,427 1200,357 L1200,523 L0,523 Z" fill="var(--pale)"/>
      <path d="M0,436 C350,466 750,447 1200,377 L1200,523 L0,523 Z" fill="var(--navy)"/>
      <path d="M0,469 C350,499 750,506 1200,436 L1200,523 L0,523 Z" fill="var(--cocoa)"/>
    </svg>

    <div class="candy candy--green" role="img" aria-label="Green candy-coated chocolate"></div>
    <div class="candy candy--blue" role="img" aria-label="Blue candy-coated chocolate"></div>
    <div class="candy candy--yellow" role="img" aria-label="Yellow candy-coated chocolate"></div>

    <h1 class="brand-name">ZIP ZAP</h1>

    <div class="candy candy--pink" role="img" aria-label="Pink candy-coated chocolate"></div>
    <div class="candy candy--brown" role="img" aria-label="Brown candy-coated chocolate"></div>

    <p class="tagline">Chocolate Candy</p>
  </main>
</body>
</html>
```